Kelvaro.ch is looking for business card letterhead and envelope C5 with WOW effect

We need a strong business card for our company Kelvaro.ch, logo is available. You want a black or dark background on which the logo Stark r% 26 # 252; appears. Letterhead and envelope in C5 format should be in a similar design, but does not have to be We need a strong business card for our company Kelvaro.ch, logo is available. A black or dark background is desired, on which the logo Stark comes across. The letterhead and the envelope in C5 format should have a similar design.

Target Market(s)

Private customers as well as entrepreneurs

Contact Information for Business Card

E-mail: info@kelvaro-example.ch
Web.www.Kelvaro-example.ch
Tel: +41 ( 0 ) 79 482 6037
Adresse:
Lindenweg 14
9406 Tarnbach

Hier kann man Icons verwenden für Email,Tel und Adressse

Font styles to use
Other font styles liked:
• Dubai,bold

Colors

Designer to choose colors to be used in the design.

Requirements
Must have
• WOW effect
Nice to have
• R% 26 # 252; back business card with our service listings. - VEHICLE LABELING - SHOP WINDOW LABELING - STICKERS AND MUCH MORE ... in red color

```html
<!DOCTYPE html>
<html lang="en">
<head>
<meta charset="utf-8">
<title>Kelvaro.ch – Business Card</title>
<link href="https://fonts.googleapis.com/css2?family=Lato:wght@400;700;900&display=swap" rel="stylesheet">
<style>
  :root {
    --page-bg: #dedede;
    --card-dark: #161616;
    --card-mid: #353535;
    --accent: #fbc81c;
    --accent-deep: #d9a910;
    --accent-clear: rgba(217, 169, 16, 0);
    --text-light: #ffffff;
    --rule: #7a7a7a;
    --mark-grey: #5c5c5c;
  }
  * { margin: 0; padding: 0; box-sizing: border-box; }
  html, body {
    width: 1200px; height: 960px; overflow: hidden;
    background: var(--page-bg);
    font-family: "Lato", sans-serif;
    color: var(--text-light);
  }
  .card {
    position: absolute;
    left: 280px;
    width: 655px; height: 375px;
    border-radius: 26px;
    overflow: hidden;
    background: linear-gradient(160deg, var(--card-mid) 0%, #262626 45%, var(--card-dark) 100%);
  }
  .card--front { top: 80px; }
  .card--back { top: 506px; }

  /* front */
  .brand {
    position: absolute; left: 56px; top: 68px;
    display: flex; align-items: center; gap: 24px;
  }
  .brand__dot { width: 56px; height: 56px; border-radius: 50%; background: var(--accent); flex: none; }
  .brand__name { font-weight: 900; font-size: 26px; letter-spacing: 0.5px; color: var(--text-light); }

  .holder { position: absolute; right: 57px; top: 154px; text-align: right; }
  .holder__name { font-weight: 700; font-size: 27px; color: var(--accent); line-height: 1.1; }
  .holder__role { font-size: 17.5px; margin-top: 2px; }

  .divider {
    position: absolute; left: 58px; right: 57px; top: 235px;
    height: 1px; background: var(--rule);
  }

  .contact { position: absolute; left: 56px; top: 254px; list-style: none; }
  .contact li {
    display: flex; align-items: center; gap: 8px;
    font-size: 17.5px; line-height: 24px;
  }
  .contact svg { width: 14px; height: 14px; flex: none; }

  .address {
    position: absolute; right: 57px; top: 281px;
    text-align: right; font-size: 17.5px; line-height: 24px; font-style: normal;
  }

  /* back */
  .pattern-area {
    position: absolute; inset: 0;
    background: radial-gradient(ellipse 340px 430px at 0% 100%,
      var(--accent) 0%, var(--accent-deep) 40%, var(--accent-clear) 88%);
  }
  .back-brand {
    position: absolute; left: 394px; top: 130px; transform: translateX(-50%);
    font-weight: 900; font-size: 48px; letter-spacing: 1px; color: var(--mark-grey);
    white-space: nowrap;
  }
  .back-web {
    position: absolute; left: 394px; top: 194px; transform: translateX(-50%);
    font-size: 17px; white-space: nowrap;
  }
</style>
</head>
<body>

<section class="card card--front">
  <div class="brand">
    <span class="brand__dot"></span>
    <span class="brand__name">KELVARO.CH</span>
  </div>

  <div class="holder">
    <p class="holder__name">Lukas Brenner</p>
    <p class="holder__role">Managing Director</p>
  </div>

  <div class="divider"></div>

  <ul class="contact">
    <li>
      <svg viewBox="0 0 16 16" aria-hidden="true"><path d="M3 1.5l3 3-1.6 1.8c.9 2 2.4 3.5 4.3 4.4L10.5 9l3 3-1.8 2.2C6.5 13.8 2.2 9.5 1.5 3.3z" fill="var(--accent)"/></svg>
      +41 ( 0 ) 79 482 6037
    </li>
    <li>
      <svg viewBox="0 0 16 16" aria-hidden="true"><rect x="1" y="3.5" width="14" height="9" fill="var(--accent)"/><path d="M1 3.5l7 5 7-5" fill="none" stroke="var(--card-dark)" stroke-width="1.2"/></svg>
      info@kelvaro-example.ch
    </li>
    <li>
      <svg viewBox="0 0 16 16" aria-hidden="true" fill="none" stroke="var(--accent)" stroke-width="1.2"><circle cx="8" cy="8" r="6.5"/><ellipse cx="8" cy="8" rx="3" ry="6.5"/><path d="M1.5 8h13M2.5 5h11M2.5 11h11"/></svg>
      www.kelvaro-example.ch
    </li>
  </ul>

  <address class="address">
    Lindenweg 14<br>
    9406 Tarnbach
  </address>
</section>

<section class="card card--back">
  <div class="pattern-area" role="img" aria-label="Decorative yellow honeycomb pattern rising from the lower left corner"></div>
  <p class="back-brand">KELVARO.CH</p>
  <p class="back-web">www.kelvaro-example.ch</p>
</section>

</body>
</html>
```